Business card for Eyelash extension salon in Halden Park,California USA

We need new business card for our salon in Halden Park. The salon name is 'Lashvera' . We would like to have...Business name: Lashvera Name of person: will provide later Address 4720 N.Alder Crest Ave Halden Park , CA 90412 Phone: will provide later (Text only) Web: www.lashverastudio.example Snapgrid icon, Circlebook icon follow us for seasonal campaign and news @lashverastudiolounge Design should look elegant, high-end, clean, simple, cohesive with my brand. Please refer my brand board. Business name color will be metallic bronzy color. Im thinking grey background or white background. Thanks

Target Market(s)

25-35. Gender neutral. People who are in Entertainment business industry.
This is High-end Eyelash extension salon in Halden Park

Industry/Entity Type

Beauty Salon

Contact Information for Business Card

Business name: Lashvera
Name of person: will provide later
Address 4720 N.Alder Crest Ave Halden Park , CA 90412
Phone: will provide later (Text only)
Web: www.lashverastudio.example
Snapgrid icon, Circlebook icon
follow us for seasonal campaign and news @lashverastudiolounge

Requirements
Must have
• Beautiful, elegant, clean and simple look but very attractive and modern
Should not have
• We don't like too clutter, too busy designs.

```html
<!DOCTYPE html>
<html lang="en">
<head>
<meta charset="utf-8">
<title>Lashvera Business Card</title>
<link rel="stylesheet" href="https://fonts.googleapis.com/css2?family=Playfair+Display:wght@400;700&display=swap">
<style>
  :root {
    --bronze: #8a6850;
    --bronze-text: #8a5a3c;
    --ink: #3a3532;
    --paper: #fbfbfa;
    --backdrop: #dcdbd8;
    --divider: #d6c3b3;
    --icon: #8b7a6d;
  }
  * { margin: 0; padding: 0; box-sizing: border-box; }
  html, body {
    width: 1200px; height: 801px; overflow: hidden;
    background: var(--backdrop);
    font-family: "Playfair Display", Georgia, serif;
  }
  .sheet {
    width: 1200px; height: 801px;
    display: flex; align-items: center; justify-content: center; gap: 48px;
  }
  .card {
    width: 540px; height: 309px;
    position: relative;
    box-shadow: 0 6px 18px rgba(0,0,0,0.12);
  }
  /* Back side */
  .card-back {
    background: var(--bronze);
    color: #fff;
    display: flex; flex-direction: column; align-items: center;
  }
  .card-back .brand-name {
    margin-top: 92px;
    font-size: 44px; font-weight: 400; letter-spacing: 1px;
  }
  .social-row {
    margin-top: 22px;
    display: flex; gap: 18px;
    font-size: 11px; letter-spacing: 1px;
  }
  .social-item { display: flex; align-items: center; gap: 6px; }
  .social-dot { width: 8px; height: 8px; background: #fff; border-radius: 2px; }
  .follow-line {
    position: absolute; bottom: 30px; left: 0; right: 0;
    text-align: center; font-size: 13px;
  }
  /* Front side */
  .card-front { background: var(--paper); color: var(--ink); }
  .card-front .brand-name {
    position: absolute; left: 34px; top: 128px;
    font-size: 44px; font-weight: 400; color: var(--bronze-text);
  }
  .divider {
    position: absolute; left: 262px; top: 52px;
    width: 2px; height: 205px; background: var(--divider);
  }
  .contact {
    position: absolute; left: 284px; top: 52px; right: 14px;
    font-size: 13px; line-height: 1.4;
    white-space: nowrap;
  }
  .person-name {
    font-size: 21px; font-weight: 700; color: var(--bronze-text); letter-spacing: .5px;
  }
  .person-role { font-size: 12.5px; margin-bottom: 22px; }
  .address { margin-bottom: 8px; }
  .contact-line { display: flex; align-items: center; gap: 10px; margin-top: 3px; }
  .contact-line svg { width: 13px; height: 13px; fill: var(--icon); flex: none; }
  .web-accent { color: var(--bronze-text); }
</style>
</head>
<body>
<main class="sheet">
  <section class="card card-back">
    <div class="brand-name">Lashvera</div>
    <div class="social-row">
      <span class="social-item"><span class="social-dot"></span>Circlebook</span>
      <span class="social-item"><span class="social-dot"></span>Snapgrid</span>
    </div>
    <p class="follow-line">Follow us for seasonal campaign and news @lashverastudiolounge</p>
  </section>

  <section class="card card-front">
    <div class="brand-name">Lashvera</div>
    <div class="divider"></div>
    <div class="contact">
      <div class="person-name">MIRA CALLOWAY</div>
      <div class="person-role">Manager</div>
      <div class="address">4720 N.Alder Crest Ave Halden Park<br>CA 90412</div>
      <div class="contact-line">
        <svg viewBox="0 0 24 24" aria-hidden="true"><path d="M6.6 10.8a15.1 15.1 0 0 0 6.6 6.6l2.2-2.2c.3-.3.7-.4 1-.2 1.1.4 2.3.6 3.6.6.6 0 1 .4 1 1V20c0 .6-.4 1-1 1C10.6 21 3 13.4 3 4c0-.6.4-1 1-1h3.5c.6 0 1 .4 1 1 0 1.3.2 2.5.6 3.6.1.3 0 .7-.2 1z"/></svg>
        <span>310-555-0142</span>
      </div>
      <div class="contact-line">
        <svg viewBox="0 0 24 24" aria-hidden="true"><path d="M2 5h20v14H2z M2 5l10 8 10-8" fill="none" stroke="#8b7a6d" stroke-width="2"/></svg>
        <span>info@lashverastudio.example</span>
      </div>
      <div class="contact-line">
        <svg viewBox="0 0 24 24" aria-hidden="true"><circle cx="12" cy="12" r="9" fill="none" stroke="#8b7a6d" stroke-width="2"/><path d="M3 12h18M12 3c3 3 3 15 0 18M12 3c-3 3-3 15 0 18" fill="none" stroke="#8b7a6d" stroke-width="1.5"/></svg>
        <span>www.<span class="web-accent">lashverastudio</span>.example</span>
      </div>
    </div>
  </section>
</main>
</body>
</html>
```